Dental Medical History Form - Content provided

Design a medical history form for a dental practice. Content is provided so all that is needed is the formatting to make it look great and easy to read.

"Patient Information" to include all information contained in top portion of the "Patient Medical History Form" docx file.

"Medical History" should follow the formatting and content of the "Exact Medical History" file as this is what the entry fields look like in our practice software and so we would like it to match.

1st page - Patient info, allergies, medications, antibiotics, joint replacement, pregnancy.

2nd page - Do you have, or have you had, any of the following? . . . . . . .
Updates

Target Market(s)

All ages but must be clear enough for elderly to read. Use as much space as possible to keep font size bigger yet keep to two pages

Industry/Entity Type

Dental

Font styles to use
Sans Serif

Requirements
Must have
• All content provided
• Our logo at the top (file provided)
• Century Gothic Font
• Limit to two pages

```html
<!DOCTYPE html>
<html lang="en">
<head>
<meta charset="utf-8">
<title>Harbourline Dental – Patient Form</title>
<link href="https://fonts.googleapis.com/css2?family=Questrial&family=Mulish:wght@400;700&display=swap" rel="stylesheet">
<style>
  :root {
    --frame: #e8e0cf;
    --paper: #ffffff;
    --panel: #f0f0f0;
    --ink: #333333;
    --soft-ink: #6b6b6b;
    --rule: #4a4a4a;
    --box-line: #bdbdbd;
    --accent: #9b8b78;
  }
  * { box-sizing: border-box; margin: 0; padding: 0; }
  html, body { width: 849px; height: 1200px; overflow: hidden; background: var(--frame); }
  body { font-family: "Mulish", Arial, sans-serif; color: var(--ink); }
  .sheet { position: relative; width: 849px; height: 1200px; background: var(--frame); }
  .page { position: absolute; left: 14px; top: 14px; width: 821px; height: 1171px; background: var(--paper); overflow: hidden; }
  .history { position: absolute; left: 0; top: 550px; width: 821px; height: 621px; background: var(--panel); }
  .pos { position: absolute; }

  /* brand */
  .brand { position: absolute; left: 35px; top: 60px; display: flex; align-items: center; gap: 14px; }
  .brand-name { font-family: "Questrial", sans-serif; font-size: 46px; color: #3a3a3a; letter-spacing: -0.5px; line-height: 1; }
  .brand-dot { width: 26px; height: 26px; border-radius: 50%; background: var(--accent); }
  .practice-address { position: absolute; right: 24px; top: 48px; text-align: right; font-weight: 700; font-size: 14px; line-height: 22px; }

  /* patient details */
  .label { position: absolute; font-weight: 700; font-size: 13px; line-height: 18px; white-space: nowrap; }
  .colon { position: absolute; font-weight: 700; font-size: 13px; line-height: 18px; }
  .line { position: absolute; height: 0; border-top: 1px solid var(--rule); }
  .sub { position: absolute; font-size: 11px; color: var(--soft-ink); line-height: 14px; }
  .plain { position: absolute; font-size: 13px; line-height: 18px; color: var(--ink); white-space: nowrap; }
  .heading { position: absolute; font-weight: 700; font-size: 13px; line-height: 18px; letter-spacing: -0.2px; }
  .divider { position: absolute; left: 420px; top: 181px; width: 0; height: 351px; border-left: 1px solid #cfcfcf; }

  /* checkboxes */
  .box { position: absolute; width: 21px; height: 20px; background: #fff; border: 1px solid var(--box-line); }
  .option { position: absolute; font-size: 13.5px; line-height: 18px; color: #5a5a5a; white-space: nowrap; }
  .entry { position: absolute; left: 105px; width: 666px; height: 26px; background: #fff; border: 1px solid #cfcfcf; }
  .tick { position: absolute; width: 18px; height: 18px; }
</style>
</head>
<body>
<div class="sheet">
  <div class="page">

    <header>
      <div class="brand"><span class="brand-name">harbourline dental</span><span class="brand-dot"></span></div>
      <address class="practice-address" style="font-style:normal">
        Harbourline Dental<br>3.04/118 Seaview Parade<br>Tarrin NSW 2261<br>(02) 49 210 345
      </address>
    </header>

    <section class="patient">
      <span class="label" style="left:37px;top:185px">Name</span><span class="colon" style="left:140px;top:185px">:</span>
      <span class="line" style="left:149px;top:199px;width:252px"></span>
      <span class="sub" style="left:149px;top:206px">Title</span>
      <span class="sub" style="left:190px;top:206px">First</span>
      <span class="sub" style="left:263px;top:206px">Middle</span>
      <span class="sub" style="left:352px;top:206px">Last</span>

      <span class="label" style="left:37px;top:234px">Address</span><span class="colon" style="left:140px;top:234px">:</span>
      <span class="line" style="left:149px;top:249px;width:252px"></span>
      <span class="line" style="left:149px;top:274px;width:252px"></span>

      <span class="label" style="left:37px;top:284px">DOB</span><span class="colon" style="left:140px;top:284px">:</span>
      <span class="line" style="left:149px;top:298px;width:252px"></span>

      <span class="label" style="left:37px;top:308px">Email Address</span><span class="colon" style="left:140px;top:308px">:</span>
      <span class="line" style="left:149px;top:323px;width:252px"></span>

      <span class="label" style="left:37px;top:333px">Phone Numbers :</span>
      <span class="plain" style="left:152px;top:333px">Mobile</span><span class="line" style="left:201px;top:347px;width:200px"></span>
      <span class="plain" style="left:152px;top:358px">Work</span><span class="line" style="left:199px;top:372px;width:202px"></span>
      <span class="plain" style="left:152px;top:383px">Home</span><span class="line" style="left:199px;top:397px;width:202px"></span>

      <span class="heading" style="left:37px;top:432px">EMERGENCY CONTACT PERSON</span>
      <span class="label" style="left:37px;top:457px">Name</span><span class="colon" style="left:136px;top:457px">:</span>
      <span class="line" style="left:149px;top:472px;width:252px"></span>
      <span class="label" style="left:37px;top:481px">Relationship</span><span class="colon" style="left:136px;top:481px">:</span>
      <span class="line" style="left:149px;top:496px;width:252px"></span>
      <span class="label" style="left:37px;top:506px">Phone number</span><span class="colon" style="left:140px;top:506px">:</span>
      <span class="line" style="left:149px;top:520px;width:252px"></span>
    </section>

    <div class="divider"></div>

    <section class="practitioner">
      <span class="heading" style="left:434px;top:184px">GENERAL PRACTITIONER</span>
      <span class="label" style="left:434px;top:216px">Name</span><span class="colon" style="left:532px;top:216px">:</span>
      <span class="line" style="left:547px;top:231px;width:238px"></span>
      <span class="label" style="left:434px;top:249px">Practice Name</span><span class="colon" style="left:532px;top:249px">:</span>
      <span class="line" style="left:547px;top:264px;width:238px"></span>
      <span class="label" style="left:434px;top:281px">Phone Number</span><span class="colon" style="left:532px;top:281px">:</span>
      <span class="line" style="left:547px;top:296px;width:238px"></span>
      <span class="label" style="left:434px;top:314px">Do you have a health fund with dental cover?</span>
      <span class="box" style="left:535px;top:347px;width:23px;height:19px;border-color:#555"></span>
      <span class="label" style="left:562px;top:347px">Yes</span>
      <span class="plain" style="left:595px;top:347px">or</span>
      <span class="box" style="left:620px;top:347px;width:23px;height:19px;border-color:#555"></span>
      <span class="label" style="left:646px;top:347px">No</span>
      <span class="label" style="left:434px;top:379px">If so, what is the name of the fund ?</span>
      <span class="line" style="left:656px;top:394px;width:129px"></span>
      <span class="label" style="left:434px;top:412px">Fund Number?</span><span class="colon" style="left:532px;top:412px">:</span>
      <span class="line" style="left:547px;top:427px;width:238px"></span>
      <span class="label" style="left:434px;top:445px">Priority Number on card&nbsp; : 0&nbsp; 1&nbsp; 2&nbsp; 3&nbsp; 4&nbsp;&nbsp; 5</span>
      <span class="box" style="left:695px;top:445px;width:23px;height:19px;border-color:#555"></span>
      <span class="label" style="left:434px;top:477px">Occupation</span><span class="colon" style="left:532px;top:477px">:</span>
      <span class="line" style="left:547px;top:492px;width:238px"></span>
      <span class="label" style="left:434px;top:510px">Referrred by</span><span class="colon" style="left:532px;top:510px">:</span>
      <span class="line" style="left:547px;top:525px;width:238px"></span>
    </section>

    <section class="history">
      <!-- allergies -->
      <span class="label" style="left:37px;top:24px">Please indicate if you are allergic to any of the following</span>
      <svg class="tick" style="left:385px;top:24px" viewBox="0 0 18 18" aria-hidden="true"><rect x="1" y="2" width="15" height="15" fill="none" stroke="#333" stroke-width="1.5"/><path d="M4 9 l3.5 4 L16 1" fill="none" stroke="#333" stroke-width="2"/></svg>
      <span class="label" style="left:407px;top:24px">?</span>

      <span class="box" style="left:105px;top:48px"></span><span class="option" style="left:135px;top:49px">Aspirin</span>
      <span class="box" style="left:283px;top:48px"></span><span class="option" style="left:314px;top:49px">Codeine</span>
      <span class="box" style="left:453px;top:48px"></span><span class="option" style="left:487px;top:49px">Penicillin</span>
      <span class="box" style="left:636px;top:48px"></span><span class="option" style="left:667px;top:49px">Sulfites</span>
      <span class="box" style="left:105px;top:74px"></span><span class="option" style="left:135px;top:74px">Latex</span>
      <span class="box" style="left:283px;top:74px"></span><span class="option" style="left:314px;top:74px">Local Anaesthetic</span>
      <span class="box" style="left:453px;top:74px"></span><span class="option" style="left:487px;top:74px">Lactose</span>
      <span class="box" style="left:636px;top:74px"></span><span class="option" style="left:667px;top:74px">Nickel</span>

      <span class="label" style="left:37px;top:126px">Other</span>
      <span class="entry" style="top:124px"></span>

      <!-- medication -->
      <span class="label" style="left:37px;top:166px">Are you currently taking, or have ever taken, any of the following medication</span>
      <svg class="tick" style="left:523px;top:167px" viewBox="0 0 18 18" aria-hidden="true"><rect x="1" y="2" width="15" height="15" fill="none" stroke="#333" stroke-width="1.5"/><path d="M4 9 l3.5 4 L16 1" fill="none" stroke="#333" stroke-width="2"/></svg>
      <span class="label" style="left:546px;top:166px">?</span>

      <span class="box" style="left:105px;top:184px"></span><span class="option" style="left:135px;top:185px">Asthma inhaler</span>
      <span class="box" style="left:283px;top:184px"></span><span class="option" style="left:314px;top:185px">Anti-epileptics</span>
      <span class="box" style="left:453px;top:184px"></span><span class="option" style="left:487px;top:185px">Anti-depressants</span>
      <span class="box" style="left:636px;top:184px"></span><span class="option" style="left:667px;top:185px">Blood Pressure</span>
      <span class="box" style="left:105px;top:213px"></span><span class="option" style="left:135px;top:214px">Blood Thinners</span>
      <span class="box" style="left:283px;top:213px"></span><span class="option" style="left:314px;top:214px">Bisphosphonates</span>
      <span class="box" style="left:453px;top:213px"></span><span class="option" style="left:487px;top:214px">Chemotherapy</span>
      <span class="box" style="left:636px;top:213px"></span><span class="option" style="left:667px;top:214px">Insulin</span>
      <span class="box" style="left:105px;top:242px"></span><span class="option" style="left:135px;top:243px">Immunosuppressants</span>
      <span class="box" style="left:283px;top:242px"></span><span class="option" style="left:314px;top:243px">Steroids</span>
      <span class="box" style="left:453px;top:242px"></span><span class="option" style="left:487px;top:243px">Oral Contraceptive</span>
      <span class="box" style="left:636px;top:242px"></span><span class="option" style="left:667px;top:243px">Other</span>

      <span class="label" style="left:37px;top:319px">Please specify medication name, dose, and frequency where possible:</span>
      <span class="entry" style="top:348px"></span>
      <span class="entry" style="top:381px"></span>
      <span class="entry" style="top:413px"></span>

      <!-- general questions -->
      <span class="label" style="left:37px;top:473px">Do you require antibiotic cover ?</span>
      <span class="box" style="left:283px;top:472px"></span><span class="option" style="left:313px;top:473px">Yes</span>
      <span class="box" style="left:355px;top:472px"></span><span class="option" style="left:384px;top:473px">No</span>

      <span class="label" style="left:37px;top:498px">Have you had a joint replacement?</span>
      <span class="box" style="left:283px;top:497px"></span><span class="option" style="left:313px;top:498px">Yes</span>
      <span class="box" style="left:355px;top:497px"></span><span class="option" style="left:384px;top:498px">No</span>

      <span class="label" style="left:37px;top:522px">WOMEN</span>

      <span class="label" style="left:37px;top:548px">Are you pregnant?</span>
      <span class="box" style="left:283px;top:547px"></span><span class="option" style="left:313px;top:548px">Yes</span>
      <span class="box" style="left:355px;top:547px"></span><span class="option" style="left:384px;top:548px">No</span>
      <span class="box" style="left:423px;top:547px"></span><span class="option" style="left:453px;top:548px">Possible</span>

      <span class="label" style="left:37px;top:572px">Breast Feeding?</span>
      <span class="box" style="left:283px;top:571px"></span><span class="option" style="left:313px;top:572px">Yes</span>
      <span class="box" style="left:355px;top:571px"></span><span class="option" style="left:384px;top:572px">No</span>
    </section>

  </div>
</div>
</body>
</html>
```